New Bicycle shop business card

Hi!
I'm looking for a business card for my new proffesional bike mechanics shop. This shop is only for fixing broken bikes and not selling bikes.
Peferbly a modern and sleek and modern design.
Colors: black, grey, red, white
Information:
Name: Rijwielwerkplaats Vanhoutte
Shop owner: Bart Vanhoutte & Marieke Segers
Website: www.rijwielwerkplaats-vanhoutte.be
Email: info@rijwielwerkplaats-vanhoutte.be
Phone number: +32471902368
Street adres: Kerkweg 46
9940 Bellebeke
Slogan/shop information: Herstellingen van alle merken.
Logo: see files.
Target Market(s)
People who seek a mechanic to fix or upgrade their bikes.
Contact Information for Business Card
Information:
Website: info@rijwielwerkplaats-vanhoutte.be
9940 Bellebeke
Logo: see files.

```html
<!DOCTYPE html>
<html lang="nl">
<head>
<meta charset="UTF-8">
<title>Rijwielwerkplaats Vanhoutte – Visitekaartje</title>
<link href="https://fonts.googleapis.com/css2?family=Montserrat:wght@600;800&family=Questrial&display=swap" rel="stylesheet">
<style>
  :root {
    --backdrop: #e4e2df;
    --frost-top: #f1f1f1;
    --frost-bottom: #d6d4d2;
    --ink: #161616;
    --panel: #141414;
    --panel-edge: #2a2a2a;
    --red: #b8232f;
    --red-dark: #8e1620;
    --silver: #e9e6e2;
    --icon-ring: #bdb6ae;
    --text-light: #ece9e6;
  }
  html, body {
    margin: 0;
    width: 970px;
    height: 1200px;
    overflow: hidden;
    background: var(--backdrop);
  }
  .card {
    position: absolute;
    left: 185px;
    top: 75px;
    width: 600px;
    height: 1050px;
    border-radius: 22px;
    overflow: hidden;
    background: linear-gradient(180deg, var(--frost-top), var(--frost-bottom));
    box-shadow: 0 18px 40px rgba(0,0,0,.18);
  }
  .brand {
    position: absolute;
    top: 95px;
    left: 0;
    width: 100%;
    text-align: center;
  }
  .brand-mark {
    width: 120px;
    height: 120px;
    margin: 0 auto 40px;
    border-radius: 50%;
    background: var(--red);
  }
  .brand-name {
    margin: 0;
    font-family: "Montserrat", sans-serif;
    font-weight: 800;
    color: var(--ink);
    font-size: 38px;
    line-height: 1.15;
    letter-spacing: 1px;
  }
  .brand-name .line2 {
    display: block;
    letter-spacing: 14px;
    margin-right: -14px;
  }
  .tagline {
    margin: 16px 0 0;
    font-family: "Montserrat", sans-serif;
    font-weight: 600;
    font-size: 18px;
    letter-spacing: 3.5px;
    color: var(--ink);
  }
  .swoosh {
    position: absolute;
    top: 440px;
    left: 0;
    width: 600px;
    height: 140px;
    display: block;
  }
  .contact-panel {
    position: absolute;
    top: 579px;
    left: 0;
    width: 600px;
    height: 390px;
    background: linear-gradient(180deg, var(--panel), var(--panel-edge));
    text-align: center;
    font-family: "Questrial", sans-serif;
    color: var(--text-light);
  }
  .owners {
    margin: 0;
    padding-top: 0;
    position: relative;
    top: -10px;
    font-size: 28px;
    letter-spacing: .5px;
  }
  .contact-row {
    margin-top: 14px;
  }
  .contact-icon {
    display: block;
    margin: 0 auto;
  }
  .contact-text {
    margin: 6px 0 0;
    font-size: 25px;
  }
  .web-band {
    position: absolute;
    bottom: 0;
    left: 0;
    width: 600px;
    height: 81px;
    border-top: 8px solid var(--silver);
    box-sizing: border-box;
    background: linear-gradient(90deg, var(--red-dark), var(--red) 50%, var(--red-dark));
    font-family: "Questrial", sans-serif;
    color: var(--text-light);
    font-size: 22px;
    line-height: 73px;
    text-align: center;
  }
</style>
</head>
<body>
  <div class="card">
    <header class="brand">
      <div class="brand-mark"></div>
      <h1 class="brand-name">RIJWIELWERKPLAATS<span class="line2">VANHOUTTE</span></h1>
      <p class="tagline">Herstellingen van alle merken</p>
    </header>

    <svg class="swoosh" viewBox="0 0 600 140" aria-hidden="true">
      <path d="M0 140 L0 112 Q260 0 600 40 L600 140 Z" fill="#141414"/>
      <path d="M0 112 Q260 0 600 40 L600 28 Q260 -14 0 86 Z" fill="#b8232f"/>
      <path d="M110 88 Q340 20 600 48" fill="none" stroke="#e9e6e2" stroke-width="3"/>
    </svg>

    <section class="contact-panel">
      <p class="owners">BART VANHOUTTE &amp; MARIEKE SEGERS</p>

      <div class="contact-row">
        <svg class="contact-icon" width="360" height="54" viewBox="0 0 360 54" aria-hidden="true">
          <line x1="10" y1="27" x2="148" y2="27" stroke="#b8232f" stroke-width="2"/>
          <line x1="212" y1="27" x2="350" y2="27" stroke="#b8232f" stroke-width="2"/>
          <circle cx="180" cy="27" r="24" fill="#bdb6ae"/>
          <circle cx="180" cy="27" r="19" fill="#f4f2ef"/>
          <path d="M172 17 l5 -2 l4 8 l-3 3 q2 5 6 8 l3 -3 l8 4 l-2 5 q-12 0 -21 -23 z" fill="#222"/>
        </svg>
        <p class="contact-text">+32471902368</p>
      </div>

      <div class="contact-row">
        <svg class="contact-icon" width="360" height="54" viewBox="0 0 360 54" aria-hidden="true">
          <line x1="10" y1="27" x2="148" y2="27" stroke="#b8232f" stroke-width="2"/>
          <line x1="212" y1="27" x2="350" y2="27" stroke="#b8232f" stroke-width="2"/>
          <circle cx="180" cy="27" r="24" fill="#bdb6ae"/>
          <circle cx="180" cy="27" r="19" fill="#f4f2ef"/>
          <rect x="169" y="19" width="22" height="16" fill="none" stroke="#222" stroke-width="2"/>
          <path d="M169 19 L180 28 L191 19" fill="none" stroke="#222" stroke-width="2"/>
        </svg>
        <p class="contact-text">info@rijwielwerkplaats-vanhoutte.be</p>
      </div>

      <div class="contact-row">
        <svg class="contact-icon" width="360" height="54" viewBox="0 0 360 54" aria-hidden="true">
          <line x1="10" y1="27" x2="148" y2="27" stroke="#b8232f" stroke-width="2"/>
          <line x1="212" y1="27" x2="350" y2="27" stroke="#b8232f" stroke-width="2"/>
          <circle cx="180" cy="27" r="24" fill="#bdb6ae"/>
          <circle cx="180" cy="27" r="19" fill="#f4f2ef"/>
          <path d="M180 39 Q171 28 171 23 A9 9 0 0 1 189 23 Q189 28 180 39 Z" fill="none" stroke="#222" stroke-width="2"/>
          <circle cx="180" cy="23" r="3" fill="#222"/>
        </svg>
        <p class="contact-text">Kerkweg 46, 9940 Bellebeke</p>
      </div>
    </section>

    <footer class="web-band">www.rijwielwerkplaats-vanhoutte.be</footer>
  </div>
</body>
</html>
```